International business needs business cards

Our company, DRV Ventures Inc. is in the business of supplying a range construction products with particular emphasis on CEMENT. We have developed our own brand - TORVAN SUPPLIES - with which to infiltrate the market. We are launching our brand of cement (TORVAN Type IS Cement) into the Caribbean which is unlike anything this market has ever seen. A monopoly has existed here for the past 60-odd years and the market has now opened to allow the importation of other brands and consumers are anxious and ready for change/improvement. We are very excited to be launching and want to make a great first impression. We will be conducting workshops and seminars (from government level to the hardware store owners) and we want our business card to give us the strong, confident introduction that we need.

Target Market(s)

construction; builders; engineers; home owners

Industry/Entity Type

Construction

Contact Information for Business Card

Marisol Depree
CEO
cell # 1 555 4180736
Ground floor,Lindell Plaza Suite 2734
George Town,Grand Cayman
Cayman Islands,KY1-4823
EMAIL: m.depree@drvventuresinc.example
web site drvventuresinc.example

COMPANY: skype info drv.ventures.example

second card
Yvette Brannock-Depree
CFO
CELL# 1 555 607 3941
George Town,Grand Cayman
Cayman Islands,KY1-4823
EMAIL: y.brannockdepree@drvventuresinc.example
website drvventuresinc.example

Requirements
Must have
• Business cards must display BOTH logos - DRV is the company and TORVAN is the brand.

```html
<!DOCTYPE html>
<html lang="en">
<head>
<meta charset="utf-8">
<title>DRV Ventures Inc. – Business Card</title>
<link href="https://fonts.googleapis.com/css2?family=Open+Sans:wght@400;600;700&display=swap" rel="stylesheet">
<style>
  :root {
    --page: #e9e6e1;
    --ink: #1a1a1a;
    --card-black: #0b0b0b;
    --card-white: #ffffff;
    --brand-red: #8e1b1f;
    --text-grey: #555555;
    --rule-grey: #cfcfcf;
    --web-grey: #d6d6d6;
  }
  * { margin: 0; padding: 0; box-sizing: border-box; }
  html, body {
    width: 1200px; height: 950px; overflow: hidden;
    background: var(--page);
    font-family: "Open Sans", Arial, sans-serif;
  }
  .canvas { position: relative; width: 1200px; height: 950px; }
  .card {
    position: absolute; left: 250px; width: 700px; height: 400px;
    overflow: hidden; box-shadow: 0 8px 24px rgba(0,0,0,.25);
  }
  /* Front */
  .card--front { top: 50px; background: var(--card-black); }
  .front-mark {
    position: absolute; left: 0; right: 0; top: 130px;
    display: flex; align-items: center; justify-content: center; gap: 16px;
  }
  .front-mark__square { width: 56px; height: 56px; background: var(--brand-red); }
  .front-mark__name { color: #ffffff; font-weight: 700; font-size: 34px; }
  .front-web {
    position: absolute; left: 0; right: 0; top: 300px; text-align: center;
    color: var(--web-grey); font-size: 17px; letter-spacing: 4px;
  }
  /* Back */
  .card--back { top: 500px; background: var(--card-white); }
  .back-swoosh { position: absolute; left: 0; top: 0; width: 700px; height: 400px; }
  .company-mark {
    position: absolute; left: 40px; top: 95px; width: 240px;
    display: flex; align-items: center; gap: 12px;
  }
  .company-mark__square { width: 56px; height: 56px; background: var(--brand-red); flex: none; }
  .company-mark__name {
    color: var(--ink); font-weight: 700; font-size: 26px; line-height: 1.1;
    max-width: 170px;
  }
  .brand-mark {
    position: absolute; left: 40px; width: 240px; top: 200px; text-align: center;
    color: var(--ink); font-weight: 700; font-size: 20px; letter-spacing: 1px;
  }
  .divider {
    position: absolute; left: 300px; top: 40px; width: 1px; height: 230px;
    background: var(--rule-grey);
  }
  .contact { position: absolute; left: 325px; top: 40px; color: var(--text-grey); }
  .contact__name { color: var(--brand-red); font-weight: 600; font-size: 24px; line-height: 1.2; }
  .contact__title { color: var(--ink); font-size: 15px; margin-bottom: 22px; }
  .contact__address { font-size: 15px; line-height: 1.4; margin-bottom: 10px; }
  .contact__line { display: flex; align-items: center; gap: 8px; font-size: 15px; line-height: 1.5; }
  .contact__icon { width: 14px; height: 14px; flex: none; }
</style>
</head>
<body>
<main class="canvas">

  <section class="card card--front" aria-label="Business card front">
    <div class="front-mark">
      <span class="front-mark__square"></span>
      <span class="front-mark__name">DRV Ventures Inc.</span>
    </div>
    <p class="front-web">www.drvventuresinc.example</p>
  </section>

  <section class="card card--back" aria-label="Business card back">
    <svg class="back-swoosh" viewBox="0 0 700 400" aria-hidden="true">
      <path d="M0,382 C240,370 470,334 700,262" fill="none" stroke="#111" stroke-width="5"/>
      <path d="M0,392 C240,382 470,348 700,280 L700,400 L0,400 Z" fill="var(--brand-red)"/>
      <path d="M0,397 C240,390 470,366 700,310 L700,322 C470,376 240,397 0,400 Z" fill="#fff" opacity=".85"/>
      <path d="M0,400 C240,395 470,378 700,338 L700,348 C470,388 240,400 0,400 Z" fill="#111"/>
    </svg>

    <div class="company-mark">
      <span class="company-mark__square"></span>
      <span class="company-mark__name">DRV Ventures Inc.</span>
    </div>
    <div class="brand-mark">TORVAN SUPPLIES</div>

    <div class="divider"></div>

    <div class="contact">
      <h1 class="contact__name">Marisol Depree</h1>
      <p class="contact__title">CEO</p>
      <p class="contact__address">Ground floor<br>Lindell Plaza Suite 2734<br>George Town,Grand Cayman<br>Cayman Islands,KY1-4823</p>
      <p class="contact__line">
        <svg class="contact__icon" viewBox="0 0 14 14"><rect x="3" y="0.5" width="8" height="13" rx="1.5" fill="none" stroke="var(--brand-red)" stroke-width="1.6"/><circle cx="7" cy="11" r="0.9" fill="var(--brand-red)"/></svg>
        1 555 4180736
      </p>
      <p class="contact__line">
        <svg class="contact__icon" viewBox="0 0 14 14"><rect x="0.5" y="2.5" width="13" height="9" fill="var(--brand-red)"/><path d="M0.5,2.5 L7,8 L13.5,2.5" fill="none" stroke="#fff" stroke-width="1.2"/></svg>
        m.depree@drvventuresinc.example
      </p>
      <p class="contact__line">
        <svg class="contact__icon" viewBox="0 0 14 14"><circle cx="7" cy="7" r="6.5" fill="var(--brand-red)"/><path d="M1,7 H13 M7,1 C4,4 4,10 7,13 M7,1 C10,4 10,10 7,13" fill="none" stroke="#fff" stroke-width="1"/></svg>
        drvventuresinc.example
      </p>
    </div>
  </section>

</main>
</body>
</html>
```